New Fun, Positive, energised looking Business Card Needed for High Achiever Coach

I am looking for a two sided full colour business card. I am self employed and have recently re branded my 1-2-1 work re-vitalising high achievers. My target client base for these cards is therefore high achievers - usually aged 40 -55, they are often entrepreneurs, CEO or work in banking and finance and 2/3 are male. I work with them on 90 day or 6 month coaching programs to help them live their success in a healthier, more sustainable and fulfiiled way. They pay for this privately so though they are corporate types the cards need not look 'corporate'. I want to portray the idea of transformation, vitality and re-connecting.
You can get a feel for the look I like on my new website: morvenlisk.co.uk
I want to use this logo with strapline (Re-Vitalising High Achievers) (I purchased off Logoharbor) and font/ colours (the turquoise and green).
Details to include on the card:
www.morvenlisk.co.uk
+44 7915 302618
morven@morvenlisk.co.uk
skype: morvenlisk
I'd also like to include:
Do you struggle to switch off? Want to be healthier and feel fitter? Want closer relationships? More clarity over the direction you are headed? I can help you do these things using integrated mind-body techniques. Visit morvenlisk.co.uk TODAY to apply for a FREE Breakthrough session.
BUT if that is too much text for a card I am open to advice/ammendments.
Updates
Thanks for your design - I am considering them. PLease change the wording to :

```html
<!DOCTYPE html>
<html lang="en">
<head>
<meta charset="utf-8">
<title>Morven Lisk – Business Card</title>
<link rel="stylesheet" href="https://fonts.googleapis.com/css2?family=Open+Sans:wght@400;600&display=swap">
<style>
  :root {
    --page: #e9e7e3;
    --card: #0c0c0c;
    --turquoise: #1ba7d2;
    --green: #5cbf6e;
    --white: #ffffff;
    --muted: #d8d8d8;
    --divider: #6a6a6a;
  }
  * { margin: 0; padding: 0; box-sizing: border-box; }
  html, body {
    width: 1200px; height: 720px; overflow: hidden;
    background: var(--page);
    font-family: "Open Sans", Arial, sans-serif;
  }
  .sheet {
    position: relative; width: 1200px; height: 720px;
    display: flex; align-items: center; justify-content: center; gap: 24px;
  }
  .card {
    position: relative; width: 560px; height: 320px;
    background: var(--card); overflow: hidden;
    box-shadow: 0 6px 18px rgba(0,0,0,0.18);
  }

  /* Front */
  .card-front .wave { position: absolute; inset: 0; }
  .brand {
    position: absolute; left: 38px; top: 108px;
    color: var(--green); font-weight: 600; font-size: 34px; line-height: 1;
  }
  .strapline {
    position: absolute; left: 40px; top: 150px;
    color: var(--turquoise); font-size: 14px; font-weight: 400;
  }
  .contact {
    position: absolute; left: 330px; top: 32px;
    border-left: 1px solid var(--divider); padding-left: 18px;
    list-style: none; color: var(--white); font-size: 13px;
  }
  .contact li { display: flex; align-items: center; gap: 9px; height: 22px; }
  .contact svg { width: 13px; height: 13px; flex: none; }
  .web {
    position: absolute; left: 70px; top: 276px;
    color: var(--white); font-size: 15px; letter-spacing: 1.5px;
  }

  /* Back */
  .back-brand {
    position: absolute; right: 40px; top: 52px;
    color: var(--green); font-weight: 600; font-size: 44px; line-height: 1;
  }
  .pitch {
    position: absolute; left: 34px; bottom: 30px; right: 30px;
    color: var(--white); font-size: 14.5px; line-height: 1.45;
  }
  .pitch .questions { margin-bottom: 12px; }
  .pitch .site { color: var(--green); font-weight: 600; }
</style>
</head>
<body>
<main class="sheet">

  <section class="card card-front" aria-label="Business card front">
    <svg class="wave" viewBox="0 0 560 320" preserveAspectRatio="none" aria-hidden="true">
      <path d="M0 192 C170 176 310 222 560 118" fill="none" stroke="var(--green)" stroke-width="4"/>
      <path d="M0 208 C170 192 310 238 560 134 L560 176 C400 236 250 296 120 320 L0 320 Z" fill="var(--turquoise)"/>
    </svg>

    <div class="brand">Morven Lisk</div>
    <div class="strapline">Re-Vitalising High Achievers</div>

    <ul class="contact">
      <li>
        <svg viewBox="0 0 16 16" aria-hidden="true"><circle cx="8" cy="8" r="8" fill="var(--green)"/><path d="M5 4.5l1.6-.3.8 2-1 .8a6 6 0 0 0 2.6 2.6l.8-1 2 .8-.3 1.6C9 11.6 4.4 7 5 4.5z" fill="var(--card)"/></svg>
        <span>+44 7915 302618</span>
      </li>
      <li>
        <svg viewBox="0 0 16 16" aria-hidden="true"><circle cx="8" cy="8" r="8" fill="var(--green)"/><rect x="4" y="5.5" width="8" height="5.5" fill="var(--card)"/><path d="M4 5.5l4 3 4-3" fill="none" stroke="var(--green)" stroke-width="1"/></svg>
        <span>morven@morvenlisk.co.uk</span>
      </li>
      <li>
        <svg viewBox="0 0 16 16" aria-hidden="true"><rect x="1" y="1" width="14" height="14" rx="2" fill="var(--turquoise)"/></svg>
        <span>morvenlisk</span>
      </li>
    </ul>

    <div class="web">www.morvenlisk.co.uk</div>
  </section>

  <section class="card card-back" aria-label="Business card back">
    <div class="back-brand">Morven Lisk</div>
    <div class="pitch">
      <p class="questions">Do you struggle to switch off?<br>
        Want to be healthier and feel fitter?<br>
        Want closer relationships?<br>
        More clarity over the direction you are headed?</p>
      <p>I can help you do these things using integrated mind-body techniques.<br>
        Visit <span class="site">morvenlisk.co.uk</span> TODAY to apply for a FREE Breakthrough session.</p>
    </div>
  </section>

</main>
</body>
</html>
```